Buch-/eBook-Cover für Traumatherapeutin
Zielgruppe
Ich bin Traumatherapeutin und schreibe ein Buch zum Thema Trauma bearbeiten.
Meine Zielgruppe sucht Heilung, Genesung, Selbstliebe etc.
Aufgabenstellung
Buchcover
Bitte erstell mir ein modernes positives inspirierendes Buchcover mit dem
Titel: 'Morgenlicht NEU entdecken“
Untertitel: „Spüre den Mut der ganz in dir wohnt“
Dr. Mira Kessow
Ich hätte gerne ein modernes Buch, das entweder einen Bezug zum Thema Trauma hat oder aber einfach stylische Schriftzüge. Bin aber auch offen für andere Vorschläge.
Dunkelblau, weiß und türkis oder auch rosa mag ich ganz gerne. Wobei Dunkelblau, weiß und türkis meine Favoriten sind und mit rosa höchstens kleinere Akzente gesetzt werden sollten.
Das Buchcover soll modern sein und direkt ansprechen. Gerne eine originelle Lösung, oder etwas Besonderes, etwas das Tiefe ausdrückt, oder man mehrmals hinsehen muss um etwas zu erkennen oder etwas das mehr Interpretationsspielraum lässt.
Gerne auch viel weiß, zumindest heller und nicht zu dunkel. Stylish, aber nicht überfrachtet.
Schreib mich gerne an, wenn du Fragen hast.
Ich habe mal zwei Beispiel von Typolösungen angehängt, die ich ganz cool fände.
Ich freue mich auf deine Ideen :-)
Ganz liebe Grüße
Mira

```html
<!DOCTYPE html>
<html lang="de">
<head>
<meta charset="utf-8">
<title>Morgenlicht NEU entdecken – Buchcover</title>
<link href="https://fonts.googleapis.com/css2?family=Allura&family=Bebas+Neue&family=Open+Sans:ital,wght@0,400;1,400&display=swap" rel="stylesheet">
<style>
  :root {
    --rose: #d3a6c4;
    --rose-line: #e48fc0;
    --mint: #a8dcd4;
    --mint-mid: #b7c9cc;
    --teal-line: #6fb9ab;
    --violet: #5b3a8c;
    --white: #ffffff;
  }
  * { margin: 0; padding: 0; box-sizing: border-box; }
  html, body { width: 858px; height: 1200px; overflow: hidden; background: var(--white); }
  .cover {
    position: relative;
    width: 858px;
    height: 1200px;
    overflow: hidden;
    background: linear-gradient(170deg, var(--rose) 0%, var(--mint-mid) 38%, var(--mint) 70%, var(--mint) 100%);
  }
  .cover__decor { position: absolute; inset: 0; width: 858px; height: 1200px; }
  .author {
    position: absolute;
    top: 52px;
    left: 0;
    width: 100%;
    padding-left: 228px;
    text-align: center;
    font-family: "Open Sans", sans-serif;
    font-size: 22px;
    color: var(--white);
    letter-spacing: 0.2px;
  }
  .title { position: absolute; left: 0; top: 0; width: 100%; }
  .title__script {
    position: absolute;
    font-family: "Allura", cursive;
    color: var(--violet);
    line-height: 1;
    white-space: nowrap;
  }
  .title__script--top { left: 62px; top: 300px; font-size: 150px; }
  .title__script--bottom { right: 62px; top: 570px; font-size: 142px; }
  .title__main {
    position: absolute;
    left: 0;
    width: 100%;
    top: 432px;
    text-align: center;
    font-family: "Bebas Neue", sans-serif;
    font-size: 182px;
    line-height: 1;
    color: var(--white);
    letter-spacing: 2px;
  }
  .subtitle {
    position: absolute;
    right: 112px;
    top: 708px;
    text-align: right;
    font-family: "Open Sans", sans-serif;
    font-style: italic;
    font-size: 27px;
    line-height: 48px;
    color: var(--violet);
  }
</style>
</head>
<body>
  <main class="cover">
    <svg class="cover__decor" viewBox="0 0 858 1200" xmlns="http://www.w3.org/2000/svg">
      <defs>
        <linearGradient id="roseFan" x1="0" y1="0" x2="1" y2="1">
          <stop offset="0" stop-color="#e48fc0" stop-opacity="0.35"/>
          <stop offset="1" stop-color="#e48fc0" stop-opacity="0.12"/>
        </linearGradient>
        <linearGradient id="tealFan" x1="0" y1="0" x2="1" y2="1">
          <stop offset="0" stop-color="#6fb9ab" stop-opacity="0.3"/>
          <stop offset="1" stop-color="#6fb9ab" stop-opacity="0.15"/>
        </linearGradient>
      </defs>
      <polygon class="decor decor--rose" role="img" aria-label="Dekoratives Muster aus feinen rosa Linien oben rechts"
               points="314,0 858,0 858,438" fill="url(#roseFan)"/>
      <polygon class="decor decor--teal" role="img" aria-label="Dekoratives Muster aus feinen türkisen Linien unten links"
               points="0,737 0,1200 482,1200" fill="url(#tealFan)"/>
      <polygon class="badge" role="img" aria-label="Bestseller-Auszeichnung"
               points="599,957 858,957 858,1088 541,1088" fill="#5b3a8c"/>
    </svg>

    <p class="author">Dr. Mira Kessow</p>

    <h1 class="title">
      <span class="title__script title__script--top">Morgenlicht</span>
      <span class="title__main">NEU</span>
      <span class="title__script title__script--bottom">entdecken</span>
    </h1>

    <p class="subtitle">Spüre den Mut<br>der ganz in dir wohnt</p>
  </main>
</body>
</html>
```